Verodex business card

Business card for sustainable investment company called "Verodex". Verodex is an exchange platform selling carbon credits between buyers and sellers. Carbon Credits are an environmental commodity for reducing global carbon emissions.

the card should obviously have our logo and the theme should be sustainability/environment mixed with a trading platform.

Contact Information for Business Card

Logo, Name, Title, Phone, Email

Colors
0054AA
0677BA
7BADD7
CADEEF
E8F1F8
0094D4
00A9DD
6FCCEA
C7EBF8
E9F6FB
00AB8E
00BBA5
67D7C9
C6EFE9
E9F9F6
59FF00
82FF00
B8FF75
E3FFCB
F4FFEA

```html
<!DOCTYPE html>
<html lang="en">
<head>
<meta charset="utf-8">
<title>Verodex business card</title>
<link rel="stylesheet" href="https://fonts.googleapis.com/css2?family=Poppins:wght@400;600&display=swap">
<style>
  :root {
    --backdrop: #2b2b2b;
    --card-white: #ffffff;
    --ink: #1f2d48;
    --ink-soft: #2a2a2a;
    --divider: #b9b9b9;
    --brand-blue: #1e8fe8;
    --grad-start: #35e8ee;
    --grad-end: #1f7be9;
    --on-blue: #ffffff;
  }
  * { margin: 0; padding: 0; box-sizing: border-box; }
  html, body {
    width: 1093px;
    height: 1200px;
    overflow: hidden;
    background: var(--backdrop);
    font-family: "Poppins", sans-serif;
  }
  .card {
    position: absolute;
    left: 265px;
    border-radius: 27px;
    overflow: hidden;
    box-shadow: 0 4px 8px rgba(0,0,0,0.45);
  }
  .card--front {
    top: 226px;
    width: 576px;
    height: 356px;
    background: var(--card-white);
  }
  .card--back {
    top: 621px;
    width: 581px;
    height: 357px;
    background: linear-gradient(to top right, var(--grad-start) 0%, var(--grad-end) 100%);
    display: flex;
    align-items: center;
    justify-content: center;
  }
  .brand {
    display: flex;
    align-items: center;
    gap: 10px;
    font-weight: 600;
    letter-spacing: 0.5px;
    line-height: 1;
  }
  .brand__dot {
    border-radius: 50%;
    flex: none;
  }
  .card--front .brand {
    position: absolute;
    left: 41px;
    top: 179px;
    transform: translateY(-50%);
    font-size: 32px;
    color: var(--ink);
  }
  .card--front .brand__dot {
    width: 38px;
    height: 38px;
    background: var(--brand-blue);
  }
  .card--back .brand {
    font-size: 46px;
    color: var(--on-blue);
    gap: 16px;
    margin-top: -2px;
  }
  .card--back .brand__dot {
    width: 56px;
    height: 56px;
    background: var(--on-blue);
  }
  .divider {
    position: absolute;
    left: 288px;
    top: 74px;
    width: 1px;
    height: 209px;
    background: var(--divider);
  }
  .person {
    position: absolute;
    left: 311px;
    top: 110px;
  }
  .person__name {
    font-size: 22px;
    font-weight: 600;
    color: var(--ink);
    line-height: 1.1;
    letter-spacing: 0.3px;
  }
  .person__title {
    font-size: 16px;
    font-weight: 400;
    color: var(--ink-soft);
    line-height: 1.1;
  }
  .contacts {
    position: absolute;
    left: 311px;
    top: 181px;
    list-style: none;
  }
  .contacts__item {
    display: flex;
    align-items: center;
    gap: 7px;
    font-size: 17px;
    line-height: 21px;
    color: var(--ink-soft);
  }
  .contacts__icon {
    width: 15px;
    height: 15px;
    flex: none;
  }
</style>
</head>
<body>
  <section class="card card--front">
    <div class="brand"><span class="brand__dot"></span><span class="brand__name">VERODEX</span></div>
    <div class="divider"></div>
    <div class="person">
      <p class="person__name">MARCUS HALE</p>
      <p class="person__title">Managing Director</p>
    </div>
    <ul class="contacts">
      <li class="contacts__item">
        <svg class="contacts__icon" viewBox="0 0 24 24" aria-hidden="true"><path fill="#1f2d48" d="M6.6 10.8a15.2 15.2 0 0 0 6.6 6.6l2.2-2.2c.3-.3.7-.4 1-.2 1.1.4 2.3.6 3.6.6.6 0 1 .4 1 1V20c0 .6-.4 1-1 1A17 17 0 0 1 3 4c0-.6.4-1 1-1h3.5c.6 0 1 .4 1 1 0 1.3.2 2.5.6 3.6.1.3 0 .7-.2 1z"/><path fill="none" stroke="#1f2d48" stroke-width="2" d="M14 3a7 7 0 0 1 7 7M14 7a3 3 0 0 1 3 3"/></svg>
        <span>044-987 654 321</span>
      </li>
      <li class="contacts__item">
        <svg class="contacts__icon" viewBox="0 0 24 24" aria-hidden="true"><rect x="1" y="5" width="22" height="14" fill="#1f2d48"/><path fill="none" stroke="#fff" stroke-width="1.6" d="M1.5 5.5 12 13l10.5-7.5M1.5 18.5l7.5-7M22.5 18.5l-7.5-7"/></svg>
        <span>hello@verodex.com</span>
      </li>
      <li class="contacts__item">
        <svg class="contacts__icon" viewBox="0 0 24 24" aria-hidden="true"><g fill="none" stroke="#1f2d48" stroke-width="1.8"><circle cx="12" cy="12" r="10"/><ellipse cx="12" cy="12" rx="4.5" ry="10"/><path d="M2 12h20M4 6.5h16M4 17.5h16"/></g></svg>
        <span>www.verodex.com</span>
      </li>
    </ul>
  </section>

  <section class="card card--back">
    <div class="brand"><span class="brand__dot"></span><span class="brand__name">VERODEX</span></div>
  </section>
</body>
</html>
```